Blue Fern Handcrafted Tomato Ketchup packaging design modern

From the best ingredients there is the best ketchup Blue Handcrafted ketchup are specially formulated for fine dining and drinks, bringing out all the flavors. As the Blue Fern handcrafted ketchup is otherwise fabulous: Made with wholesome, fully ripe fruits Nothing with half things! All Blue Fern handcrafted ketchups are pure nature, without any artificial diluents or concentrates. Where tomato is on it, that's all there is to it - guaranteed! the design should be professional and noble despite being trendy. A watcher wants to sell the ketchup as merchandising from our restaurant. but as a single brand positioning. The ketchup is vegan. Dimensions: 6.8 cm Height: 7.8 cm Circumference: 21.6 cm The text down (Text 1-4). The lid of the text the glass packaging is black! Thanks for your efforts. I look forward to your designs.

Target Market(s)

foodies

Font styles to use
Serif
Sans Serif

Colors

Designer to choose colors to be used in the design.

Requirements
Must have
• Title: (Handcrafted Tomato Ketchup) Text One: (Store chilled after opening and consume quickly, pasteurized.) Text Two: (Handcrafted in Switzerland by Varentoli Kulina GmbH, Chur www.bluefern-vorel.example) Text Tree: (Tomatoes, White Wine Vinegar, Aceto Balsamico, Brown Cane Sugar, Corn Starch, Spices, Salt) Text For: (200 grams) or (200g) The Logo of Blue Fern with the Pasta and Wine have to because of the gesety.
Nice to have
• small vegan icon (maybe)
Should not have
• text of the logo (pasta & wine)

```html
<!DOCTYPE html>
<html lang="en">
<head>
<meta charset="utf-8">
<title>Blue Fern – Handcrafted Tomato Ketchup Label</title>
<link href="https://fonts.googleapis.com/css2?family=Libre+Baskerville&family=Federo&display=swap" rel="stylesheet">
<style>
  :root {
    --page-bg: #eceef1;
    --label-tan: #d3b994;
    --border-light: #f2d6ad;
    --border-warm: #e6b377;
    --ink: #1d1b19;
    --rule: #3a3632;
  }
  html, body {
    margin: 0;
    padding: 0;
    width: 1200px;
    height: 1200px;
    overflow: hidden;
    background: var(--page-bg);
  }
  .label {
    position: absolute;
    left: 120px;
    top: 50px;
    width: 960px;
    height: 1100px;
    overflow: hidden;
    background: var(--label-tan);
    box-shadow: 0 6px 24px rgba(0,0,0,0.12);
  }
  .border-art {
    position: absolute;
    top: 0;
    width: 150px;
    height: 1100px;
    background: linear-gradient(180deg, var(--border-warm) 0%, var(--border-light) 22%, var(--border-light) 78%, var(--border-warm) 100%);
  }
  .border-art--left { left: 0; }
  .border-art--right { right: 0; }
  .label-text {
    position: absolute;
    left: 0;
    width: 100%;
    margin: 0;
    text-align: center;
    color: var(--ink);
    font-family: "Federo", sans-serif;
    font-weight: 400;
  }
  .brand-name {
    top: 210px;
    font-family: "Libre Baskerville", serif;
    font-size: 80px;
    letter-spacing: 0;
    line-height: 1;
  }
  .brand-rule {
    position: absolute;
    left: 200px;
    width: 560px;
    top: 322px;
    height: 2px;
    background: var(--rule);
  }
  .product-title {
    top: 342px;
    font-size: 33px;
    font-style: italic;
    font-weight: 700;
    letter-spacing: 0.5px;
  }
  .storage-note {
    top: 495px;
    font-size: 28px;
    line-height: 40px;
  }
  .producer {
    top: 694px;
    font-size: 20px;
    line-height: 28px;
  }
  .ingredients {
    top: 810px;
    font-size: 20px;
    line-height: 28px;
  }
  .net-weight {
    top: 925px;
    font-size: 19px;
  }
</style>
</head>
<body>
  <main class="label">
    <div class="border-art border-art--left" role="img" aria-label="Decorative geometric border pattern in pale and warm orange tones"></div>
    <div class="border-art border-art--right" role="img" aria-label="Decorative geometric border pattern in pale and warm orange tones"></div>

    <h1 class="label-text brand-name">BLUE FERN</h1>
    <div class="brand-rule"></div>
    <h2 class="label-text product-title">HANDCRAFTED TOMATO KETCHUP</h2>

    <p class="label-text storage-note">Store chilled<br>after opening and consume quickly, pasteurized.</p>

    <p class="label-text producer">Handcrafted in Switzerland<br>by Varentoli Kulina GmbH, Chur<br>www.bluefern-vorel.example</p>

    <p class="label-text ingredients">Tomatoes, White Wine Vinegar, Aceto Balsamico,<br>Brown Cane Sugar, Corn Starch, Spices, Salt</p>

    <p class="label-text net-weight">200 grams</p>
  </main>
</body>
</html>
```